Redesign This Psychology Website

We would like a slight redesign of this successful psychology (relationship counselling) website:

www.TheKelvaleClinic.com.au

We are updating the website, and we'd like a slight refresh of the design and style.

Please keep to very similar colours, and use the same logo. We're looking for around 10 page templates, however the main one is the home page.

Keep in mind, this website already converts quite well, so we want a new, fresh design in keeping with this one. Please don't bother designing something too extremely different.

thanks :)

Target Market(s)

couples who are looking for relationship counselling. Men and women, 25 - 70, across Australia

Industry/Entity Type

Psychology

Number of Pages Required

5+ page

Font styles to use
Sans Serif

Colors
87cfc6
b7a5cd
ec1f27
ffffff
cee9f5

Requirements
Must have
• a similar look to the current design, just looking for a slight refresh.
• Search bar
• Areas for lots of photos
• same logo
• lots of content areas
Nice to have
• great content areas, where we can display a lot of content and our areas.
Should not have
• no colors like orange, etc.
• should not have a totally different feel.

```html
<!DOCTYPE html>
<html lang="en">
<head>
<meta charset="utf-8">
<title>The Kelvale Clinic – Relationship &amp; Marriage Counselling</title>
<link href="https://fonts.googleapis.com/css2?family=Nunito+Sans:wght@400;600;700&family=Montserrat:wght@500;600;700&display=swap" rel="stylesheet">
<style>
:root{
  --teal:#87cfc6;
  --teal-dark:#5fb8ad;
  --lilac:#b7a5cd;
  --lilac-dark:#8f7bb3;
  --red:#ec1f27;
  --green:#77c043;
  --sky:#cee9f5;
  --white:#ffffff;
  --ink:#3c3c3c;
  --muted:#8a8a8a;
  --rule:#e2e2e2;
  --grey-bg:#efefef;
  --foot-bg:#f4f4f4;
}
*{box-sizing:border-box;margin:0;padding:0}
html,body{width:1200px;height:4369px;overflow:hidden}
body{font-family:"Nunito Sans",Arial,sans-serif;color:var(--ink);background:var(--white);position:relative}
.abs{position:absolute}
.photo{position:absolute;display:block}
a{color:inherit;text-decoration:none}

/* top bar */
.topbar{position:absolute;top:0;left:0;width:1200px;height:35px;background:#f3f3f3;border-bottom:1px solid var(--rule);font-size:13px;color:#666}
.topbar .assoc{position:absolute;left:131px;top:9px}
.topbar .links{position:absolute;right:128px;top:0;display:flex;height:35px}
.topbar .links a{padding:9px 12px;border-left:1px solid var(--rule)}

/* header */
.header{position:absolute;top:35px;left:0;width:1200px;height:125px}
.brand{position:absolute;left:118px;top:30px;display:flex;align-items:center;gap:12px}
.brand-dot{width:46px;height:46px;border-radius:50%;background:var(--teal)}
.brand-name{font-family:"Montserrat",sans-serif;font-weight:600;font-size:26px;color:var(--teal-dark);line-height:1}
.brand-tag{font-size:12px;color:var(--lilac-dark);margin-top:5px}
.search{position:absolute;left:458px;top:48px;width:356px;height:38px;border:1px solid #d6d6d6;border-radius:3px;font-size:13px;color:#999;padding:10px 12px 0 34px}
.search svg{position:absolute;left:11px;top:11px}
.callnow{position:absolute;right:130px;top:40px;text-align:right}
.callnow small{display:block;font-size:15px;color:var(--teal-dark)}
.callnow b{font-family:"Montserrat",sans-serif;font-size:24px;color:var(--red);font-weight:600;display:flex;align-items:center;gap:8px}

/* nav */
.nav{position:absolute;top:160px;left:0;width:1200px;height:65px;background:linear-gradient(180deg,#93d5cc,#7cc7bd)}
.nav ul{list-style:none;display:flex;position:absolute;left:118px;top:0;height:65px}
.nav li{font-family:"Montserrat",sans-serif;font-size:15px;font-weight:600;color:var(--white);text-transform:uppercase;line-height:17px;padding:14px 15px 0;border-right:1px solid rgba(255,255,255,.45)}
.nav li.single{padding-top:23px}
.nav li:last-child{border-right:0}

/* hero */
.hero{position:absolute;top:225px;left:0;width:1200px;height:518px;overflow:hidden}
.hero-title{position:absolute;left:118px;top:272px;font-family:"Montserrat",sans-serif;font-size:38px;font-weight:700;color:var(--white);line-height:46px;text-transform:uppercase;text-shadow:0 2px 6px rgba(0,0,0,.35)}
.finder{position:absolute;left:757px;top:101px;width:292px;height:350px;background:rgba(160,140,196,.9);padding:20px 24px;color:var(--white)}
.finder h3{font-family:"Montserrat",sans-serif;font-size:20px;font-weight:600;text-align:center;line-height:26px;margin-bottom:14px}
.finder label{display:block;font-size:13px;margin:8px 0 4px}
.finder .field{height:30px;background:var(--white);border-radius:2px;font-size:12px;color:#888;padding:7px 10px;position:relative}
.finder .btn{margin-top:14px;height:36px;background:var(--red);text-align:center;font-family:"Montserrat",sans-serif;font-weight:600;font-size:15px;line-height:36px}
.dots{position:absolute;left:545px;top:472px;display:flex;gap:9px}
.dots i{width:11px;height:11px;border-radius:50%;background:rgba(255,255,255,.6)}
.dots i:first-child{background:var(--white)}

/* intro */
.intro-video{left:140px;top:792px;width:437px;height:271px}
.play{position:absolute;left:320px;top:903px;width:70px;height:70px;border-radius:50%;border:3px solid var(--white)}
.intro{position:absolute;left:617px;top:805px;width:460px}
.intro h2{font-family:"Montserrat",sans-serif;font-weight:500;font-size:27px;line-height:34px;color:#444;margin-bottom:22px}
.intro p{font-size:15px;line-height:26px;color:#777}
.divider{position:absolute;left:131px;top:1121px;width:938px;height:1px;background:var(--rule)}
.divider-notch{position:absolute;left:583px;top:1112px}

/* service cards */
.svc{position:absolute;top:1171px;width:224px;height:344px;border:1px solid var(--rule);background:var(--white)}
.svc .photo{left:0;top:0;width:222px;height:160px}
.svc h4{position:absolute;left:18px;top:176px;font-family:"Montserrat",sans-serif;font-weight:500;font-size:19px;line-height:22px}
.svc p{position:absolute;left:18px;top:226px;width:190px;font-size:10.5px;line-height:14px;color:var(--muted)}
.btn-sm{position:absolute;display:inline-block;height:30px;padding:0 18px;line-height:30px;border-radius:3px;font-size:12px;font-weight:700;color:var(--white)}
.svc .btn-sm{left:18px;top:290px}

/* purple band */
.band{position:absolute;top:1553px;left:0;width:1200px;height:466px;background:linear-gradient(160deg,#a892c8 0%,#b7a5cd 45%,#8fcfc3 100%);overflow:hidden}
.band .photo{left:0;top:0;width:1200px;height:466px;clip-path:polygon(780px 0,1200px 0,1200px 466px,640px 466px)}
.band h2{position:absolute;left:131px;top:68px;font-family:"Montserrat",sans-serif;font-weight:500;font-size:30px;color:var(--white)}
.band .sub{position:absolute;left:131px;top:110px;font-size:17px;color:var(--white)}
.band ul{position:absolute;top:160px;list-style:none;color:var(--white);font-size:14px}
.band li{height:31px}
.band li::before{content:"›";margin-right:9px;font-weight:700}

/* feature pair */
.pair{position:absolute;top:2074px;width:460px;height:213px;border:1px solid var(--rule);overflow:hidden;background:var(--white)}
.pair h4{position:absolute;font-family:"Montserrat",sans-serif;font-weight:500;font-size:19px;line-height:23px;color:#333}
.pair p{position:absolute;font-size:11px;line-height:15px;color:var(--muted)}

/* trio */
.trio{position:absolute;top:2330px;height:432px;border:1px solid var(--rule);background:var(--white)}
.trio .photo{left:0;top:0;width:100%;height:204px}
.trio h4{position:absolute;left:24px;top:228px;font-family:"Montserrat",sans-serif;font-weight:500;font-size:20px}
.trio p{position:absolute;left:24px;top:262px;width:255px;font-size:12px;line-height:17px;color:var(--muted)}
.trio .btn-sm{left:24px;top:372px;height:34px;line-height:34px;padding:0 26px;font-size:13px}

/* topic tiles */
.topics{position:absolute;top:2796px;left:0;width:1200px;height:379px;background:var(--grey-bg)}
.tile{position:absolute;top:64px;width:292px;height:234px;overflow:hidden}
.tile .photo{left:0;top:0;width:292px;height:234px}
.tile .cap{position:absolute;left:0;bottom:0;width:100%;height:56px;background:rgba(160,140,196,.88);color:var(--white);font-size:16px;font-weight:600;text-align:center;line-height:56px}
.bars{position:absolute;left:532px;top:330px;display:flex;gap:6px}
.bars i{width:28px;height:4px;background:#c9c9c9}
.bars i:nth-child(2){background:var(--red)}

/* blogs */
.blogs-title{position:absolute;left:140px;top:3204px;font-family:"Montserrat",sans-serif;font-weight:500;font-size:32px;color:var(--red)}
.post{position:absolute;top:3262px;width:222px;height:268px}
.post .photo{left:0;top:0;width:222px;height:146px}
.date{position:absolute;left:0;top:100px;width:46px;height:46px;background:var(--teal);color:var(--white);text-align:center;font-weight:700;font-size:18px;line-height:22px;padding-top:5px}
.date small{display:block;font-size:10px;line-height:10px;font-weight:600}
.post h5{position:absolute;left:0;top:158px;font-size:14px;font-weight:700;color:#333}
.post p{position:absolute;left:0;top:180px;width:215px;font-size:10.5px;line-height:14px;color:var(--muted)}
.post .more{position:absolute;left:0;top:238px;font-size:11px;color:var(--teal-dark);font-weight:700}
.mini{position:absolute;width:296px;height:116px}
.mini .photo{left:0;top:0;width:150px;height:116px}
.mini h6{position:absolute;left:166px;top:10px;width:130px;font-size:14px;line-height:18px;font-weight:700;color:#333}
.mini .more{position:absolute;left:166px;font-size:11px;color:var(--teal-dark);font-weight:700}

/* footer */
.footer{position:absolute;top:4020px;left:0;width:1200px;height:262px;background:var(--foot-bg)}
.footer .brand{left:131px;top:80px}
.fcol{position:absolute;top:50px}
.fcol h6{font-family:"Montserrat",sans-serif;font-size:15px;font-weight:600;color:#555;margin-bottom:12px;letter-spacing:.5px}
.fcol li{list-style:none;font-size:13px;color:#666;line-height:25px}
.social{display:flex;gap:8px;margin-top:10px}
.social i{width:30px;height:30px;border-radius:50%;display:block}
.copy{position:absolute;top:4282px;left:0;width:1200px;height:87px;background:#eaeaea;text-align:center;font-size:12px;color:#777;line-height:87px}
</style>
</head>
<body>

<div class="topbar">
  <span class="assoc">Join Our Associate Program ›</span>
  <nav class="links"><a>Home</a><a>Cart</a><a>Blog</a><a>Resources</a><a>Contact</a></nav>
</div>

<header class="header">
  <div class="brand">
    <span class="brand-dot"></span>
    <div><div class="brand-name">The Kelvale Clinic</div><div class="brand-tag">helping you create loving relationships</div></div>
  </div>
  <div class="search">
    <svg width="13" height="13" viewBox="0 0 13 13"><circle cx="5.5" cy="5.5" r="4.3" fill="none" stroke="#999" stroke-width="1.5"/><line x1="8.7" y1="8.7" x2="12.3" y2="12.3" stroke="#999" stroke-width="1.5"/></svg>
    Search Here
  </div>
  <div class="callnow">
    <small>Call Us Now</small>
    <b><svg width="20" height="20" viewBox="0 0 24 24"><path d="M6.6 10.8a15 15 0 006.6 6.6l2.2-2.2c.3-.3.7-.4 1-.2 1.1.4 2.3.6 3.6.6.6 0 1 .4 1 1V20c0 .6-.4 1-1 1A17 17 0 013 4c0-.6.4-1 1-1h3.5c.6 0 1 .4 1 1 0 1.3.2 2.5.6 3.6.1.3 0 .7-.2 1z" fill="#ec1f27"/></svg>1300 555 014</b>
  </div>
</header>

<nav class="nav">
  <ul>
    <li>Counselling<br>Types</li>
    <li>Relationship Counselling<br>Locations</li>
    <li>Sex Therapy<br>Locations</li>
    <li class="single">About Us</li>
    <li class="single">Quizzes</li>
    <li class="single">FAQ's</li>
    <li class="single">Contact</li>
  </ul>
</nav>

<section class="hero">
  <div class="photo" style="left:0;top:0;width:1200px;height:518px;background:linear-gradient(120deg,#6f8f4a 0%,#b7a77c 35%,#d8c7a5 55%,#7f9a5c 80%,#5d7a3c 100%)" role="img" aria-label="Smiling couple embracing outdoors in a sunny park"></div>
  <h1 class="hero-title">Relationship &amp;<br>Marriage Counselling</h1>
  <form class="finder">
    <h3>Find Our Psychologist<br>Near You</h3>
    <label>Type of Counselling</label>
    <div class="field">Select<svg style="position:absolute;right:10px;top:11px" width="10" height="6" viewBox="0 0 10 6"><path d="M0 0l5 6 5-6z" fill="#888"/></svg></div>
    <label>Location</label>
    <div class="field"></div>
    <label>Postcode</label>
    <div class="field"></div>
    <div class="btn">SEARCH</div>
  </form>
  <div class="dots"><i></i><i></i><i></i><i></i></div>
</section>

<div class="photo intro-video" style="background:linear-gradient(135deg,#c9d6d8,#e8d9c8 55%,#b99c86)" role="img" aria-label="Video still of a psychologist speaking to camera"></div>
<div class="play"><svg style="position:absolute;left:24px;top:18px" width="24" height="28" viewBox="0 0 24 28"><path d="M0 0l24 14L0 28z" fill="#fff"/></svg></div>
<div class="intro">
  <h2>We Specialise in Relationship<br>&amp; Marriage Counselling</h2>
  <p>At The Kelvale Clinic, we are a group of PSYCHOLOGISTS, Australia wide who are passionate about relationships and helping you with yours. Our vision is to provide the most highly-regarded and comprehensive marriage counselling and relationship counselling, and sex therapy in Australia, at reasonable and affordable rates.</p>
</div>
<div class="divider"></div>
<svg class="divider-notch abs" width="34" height="14" viewBox="0 0 34 14"><path d="M0 9h10l7 5 7-5h10" fill="#fff" stroke="#e2e2e2"/></svg>

<article class="svc" style="left:131px">
  <div class="photo" style="background:linear-gradient(135deg,#d9c3b4,#8f7b70)" role="img" aria-label="Couple in a tense conversation"></div>
  <h4 style="color:var(--lilac-dark)">Relationship<br>Counselling</h4>
  <p>Communication, recovering from an affair, loss of intimacy and power battles, feeling apart.</p>
  <a class="btn-sm" style="background:var(--lilac-dark)">Learn More</a>
</article>
<article class="svc" style="left:369px">
  <div class="photo" style="background:linear-gradient(135deg,#eae4dc,#b9aea2)" role="img" aria-label="Couple lying apart in bed"></div>
  <h4 style="color:var(--red)">Sex Therapy<br>Counselling</h4>
  <p>Low libido, erectile difficulties, premature ejaculation, differing libidos, porn addiction.</p>
  <a class="btn-sm" style="background:var(--red)">Learn More</a>
</article>
<article class="svc" style="left:606px">
  <div class="photo" style="background:linear-gradient(135deg,#a8a59e,#5b5650)" role="img" aria-label="Couple arguing angrily"></div>
  <h4 style="color:var(--green)">Anger Management<br>Counselling</h4>
  <p>Managing angry outbursts, expressing your anger in healthy ways.</p>
  <a class="btn-sm" style="background:var(--green)">Learn More</a>
</article>
<article class="svc" style="left:843px">
  <div class="photo" style="background:linear-gradient(135deg,#7d6a5e,#2f2824)" role="img" aria-label="Man looking at himself in a mirror"></div>
  <h4 style="color:var(--teal-dark)">Narcissism<br>Counselling</h4>
  <p>Managing narcissistic, superior, entitled, arrogant and lack of empathy tendencies.</p>
  <a class="btn-sm" style="background:var(--teal-dark)">Learn More</a>
</article>

<section class="band">
  <div class="photo" style="background:linear-gradient(120deg,#d6cfc7,#a9b7c2 50%,#e8ddd2)" role="img" aria-label="Mature couple smiling together by the sea"></div>
  <h2>Our Kelvale Relationship Psychologists</h2>
  <div class="sub">Here are some of the common ones:</div>
  <ul style="left:131px">
    <li>Affairs</li><li>Controlling behaviour</li><li>Verbal abuse</li><li>Imbalance of power</li><li>Lack of intimacy</li><li>Poor communication</li><li>Loss of love</li>
  </ul>
  <ul style="left:344px">
    <li>Relationship neglect</li><li>Sexual problems</li><li>Problems from childhood</li><li>Problems with parenting your children</li><li>Step children and in-laws</li><li>All forms of family problems</li><li>Anger management problems</li>
  </ul>
</section>

<article class="pair" style="left:131px">
  <h4 style="left:38px;top:22px">Anxiety and<br>Depression</h4>
  <p style="left:38px;top:78px;width:150px">Caring support for worry, low mood and stress in life.</p>
  <a class="btn-sm" style="left:38px;top:160px;background:var(--lilac-dark)">Learn More</a>
  <div class="photo" style="left:215px;top:0;width:245px;height:213px;clip-path:polygon(50px 0,245px 0,245px 213px,0 213px);background:linear-gradient(135deg,#7b7470,#2e2a28)" role="img" aria-label="Man sitting with head in hands"></div>
</article>
<article class="pair" style="left:612px">
  <div class="photo" style="left:0;top:0;width:245px;height:213px;clip-path:polygon(0 0,195px 0,245px 213px,0 213px);background:linear-gradient(135deg,#b49a86,#4d3f36)" role="img" aria-label="Woman sitting sadly alone"></div>
  <h4 style="left:276px;top:22px">GP Referral Info</h4>
  <p style="left:276px;top:56px;width:160px">How a GP referral can lower your session costs today.</p>
  <a class="btn-sm" style="left:276px;top:150px;background:var(--lilac)">Learn More</a>
</article>

<article class="trio" style="left:131px;width:306px">
  <div class="photo" style="background:linear-gradient(135deg,#a9dcef,#cee9f5 60%,#e9a9b0)" role="img" aria-label="Couple holding a heart-shaped sign"></div>
  <h4 style="color:var(--red)">Communication</h4>
  <p>Most people find that their ways of communicating with each other and what hamper us from having a happy healthy relationship. Effective interpersonal</p>
  <a class="btn-sm" style="background:var(--red)">Learn More</a>
</article>
<article class="trio" style="left:451px;width:301px">
  <div class="photo" style="background:linear-gradient(135deg,#d3c7b6,#8e8272)" role="img" aria-label="Couple sitting apart on a sofa"></div>
  <h4 style="color:var(--teal-dark)">Our Relationships</h4>
  <p>We can also assist you if you want individual help and guidance on your relationship, so you can learn what the patterns in your relationships.</p>
  <a class="btn-sm" style="background:var(--teal)">Learn More</a>
</article>
<article class="trio" style="left:769px;width:303px">
  <div class="photo" style="background:radial-gradient(circle at 50% 45%,#b07a3a,#2a2018 70%)" role="img" aria-label="Glowing location pin above an open hand"></div>
  <h4 style="color:var(--lilac-dark)">Locations</h4>
  <p>We currently have relationship counselling and marriage counselling services in:<br>Sydney – 19 centres &nbsp;&nbsp;&nbsp; Brisbane – 14 centres<br>Canberra – 2 centres &nbsp;&nbsp;&nbsp; Wollongong – 1 centre</p>
  <a class="btn-sm" style="background:var(--lilac-dark)">Learn More</a>
</article>

<section class="topics">
  <div class="tile" style="left:131px"><div class="photo" style="background:linear-gradient(135deg,#c7c2bd,#5f5954)" role="img" aria-label="Upset woman holding her head"></div><div class="cap">How to Deal with an Affair?</div></div>
  <div class="tile" style="left:439px"><div class="photo" style="background:linear-gradient(135deg,#b38f6f,#4e3a2c)" role="img" aria-label="Two men smiling together"></div><div class="cap">Same Sex Relationship</div></div>
  <div class="tile" style="left:745px"><div class="photo" style="background:linear-gradient(135deg,#9a8f87,#3f3a37)" role="img" aria-label="Man looking at his reflection"></div><div class="cap">Are You living with a narcissist?</div></div>
  <div class="bars"><i></i><i></i><i></i><i></i></div>
</section>

<h2 class="blogs-title">Latest Blogs</h2>

<article class="post" style="left:137px">
  <div class="photo" style="background:linear-gradient(135deg,#d4b9a0,#7b5d48)" role="img" aria-label="Hands holding a broken paper heart"></div>
  <div class="date">15<small>APR</small></div>
  <h5>Your Blog Title here</h5>
  <p>Short blog summary text goes here with a few lines to preview the article content.</p>
  <a class="more">Read More</a>
</article>
<article class="post" style="left:373px">
  <div class="photo" style="background:linear-gradient(135deg,#8c8782,#3a3633)" role="img" aria-label="Couple arguing in a kitchen"></div>
  <div class="date">18<small>APR</small></div>
  <h5>Your Blog Title here</h5>
  <p>Short blog summary text goes here with a few lines to preview the article content.</p>
  <a class="more">Read More</a>
</article>
<article class="post" style="left:609px">
  <div class="photo" style="background:linear-gradient(135deg,#a39a90,#4c453f)" role="img" aria-label="Couple talking seriously on a couch"></div>
  <div class="date">16<small>APR</small></div>
  <h5>Your Blog Title here</h5>
  <p>Short blog summary text goes here with a few lines to preview the article content.</p>
  <a class="more">Read More</a>
</article>
<article class="post" style="left:845px">
  <div class="photo" style="background:linear-gradient(180deg,#f2a54a,#d9682a 55%,#3a2a22)" role="img" aria-label="Couple silhouetted against a sunset"></div>
  <div class="date">05<small>APR</small></div>
  <h5>Your Blog Title here</h5>
  <p>Short blog summary text goes here with a few lines to preview the article content.</p>
  <a class="more">Read More</a>
</article>

<article class="mini" style="left:137px;top:3540px"><div class="photo" style="background:linear-gradient(135deg,#8e8985,#413d3a)" role="img" aria-label="Couple in a tense moment"></div><h6>What can I do if I'm living with a Narcissist?</h6><a class="more" style="top:78px">Read More</a></article>
<article class="mini" style="left:452px;top:3540px"><div class="photo" style="background:linear-gradient(135deg,#c8beb4,#6f655c)" role="img" aria-label="Couple sitting apart"></div><h6>Why am I with a Narcissist?</h6><a class="more" style="top:60px">Read More</a></article>
<article class="mini" style="left:771px;top:3540px"><div class="photo" style="background:linear-gradient(135deg,#9c8a7c,#3c322b)" role="img" aria-label="Man looking away thoughtfully"></div><h6>How Do I Know If I'm With a Narcissist?</h6><a class="more" style="top:78px">Read More</a></article>

<article class="mini" style="left:137px;top:3665px"><div class="photo" style="background:linear-gradient(135deg,#6f6a66,#2a2725)" role="img" aria-label="Woman looking distressed"></div><h6>Are You Living With a Steamroller?</h6><a class="more" style="top:78px">Read More</a></article>
<article class="mini" style="left:452px;top:3665px"><div class="photo" style="background:linear-gradient(135deg,#b4a89c,#5b5047)" role="img" aria-label="Couple having a difficult talk"></div><h6>Letter for a Partner Doubtful About Relationship Counselling</h6><a class="more" style="top:96px">Read More</a></article>
<article class="mini" style="left:771px;top:3665px"><div class="photo" style="background:linear-gradient(135deg,#c4a58c,#6a4f3c)" role="img" aria-label="Couple smiling together"></div><h6>Do You Wonder Why You and Your Partner Are Together?</h6><a class="more" style="top:96px">Read More</a></article>

<article class="mini" style="left:137px;top:3793px"><div class="photo" style="background:linear-gradient(135deg,#bdb5ad,#625a53)" role="img" aria-label="Couple standing back to back"></div><h6>Did Your Relationship Start on Rocky Ground?</h6><a class="more" style="top:78px">Read More</a></article>
<article class="mini" style="left:452px;top:3793px"><div class="photo" style="background:linear-gradient(135deg,#d1c3b3,#847462)" role="img" aria-label="Couple relaxing at home"></div><h6>What Are You Like in a Relationship?</h6><a class="more" style="top:60px">Read More</a></article>
<article class="mini" style="left:771px;top:3793px"><div class="photo" style="background:linear-gradient(135deg,#8e7e70,#352c25)" role="img" aria-label="Couple turned away from each other"></div><h6>Is Your Pursuit of Success Sabotaging Your Relationships That Matter Most?</h6><a class="more" style="top:96px">Read More</a></article>

<footer class="footer">
  <div class="brand">
    <span class="brand-dot"></span>
    <div><div class="brand-name">The Kelvale Clinic</div><div class="brand-tag">helping you create loving relationships</div></div>
  </div>
  <div class="fcol" style="left:454px"><h6>QUICK LINKS</h6><ul><li>Home</li><li>About Us</li><li>Our Blogs</li><li>Shop Cart</li><li>Contact Us</li></ul></div>
  <div class="fcol" style="left:620px"><h6>RESOURCES</h6><ul><li>Counselling Type</li><li>Sex Therapy</li><li>Quizzes</li><li>FAQ</li><li>Relationship Counselling</li></ul></div>
  <div class="fcol" style="left:824px"><h6>CONTACT US</h6><ul><li>14 Harbour Lane Suite 2</li><li>1300 555 014</li><li>Email: hello@kelvaleclinic.example</li></ul>
    <div class="social"><i style="background:#3fa9e0"></i><i style="background:#3b5998"></i><i style="background:#0e76a8"></i><i style="background:#d64937"></i></div>
  </div>
</footer>
<div class="copy">© 2017 Company Name . All right reserved</div>

</body>
</html>
```